Internal Company (Private/Invite only) blog

I need a template for an internal company blog.
We are an FMCG organisation operating in Saudi Arabia. We have large number of partners working with us across multiple countries.
This blog is primarily designed to inform our shareholders of progress/updates, new information etc.
It will be published/updated weekly

Target Market(s)

audience is company stakeholders only

Industry/Entity Type

It Company

Requirements
Must have
• - Core feature must be that this can be secure/private as we wish to submit information that is only for a registered list of readers.

- ability to update content with images and content
Nice to have
• Some elements we have thought of
- Contact details
- Personnel Bio's
- Weekly product review
- Status on activities
- Case studies
- Future discussion points
- Glossary of terms
- submit your question/idea

Also would like to have ability to have published posts sent to the readers either as a link or as an email with the new content in the message body of the email
Should not have
• No complicated interface.
Should be easy, clean and simple layout
No business type imagery such as pie charts, graphs etc

```html
<!DOCTYPE html>
<html lang="en">
<head>
<meta charset="utf-8">
<title>Internal Blog</title>
<link href="https://fonts.googleapis.com/css2?family=Arimo:wght@400;700&display=swap" rel="stylesheet">
<style>
:root{
  --ink:#1b1b1b;
  --title:#1f2a38;
  --meta:#8a8a8a;
  --link:#1a56a8;
  --more:#2e8fd6;
  --panel:#7d7d7d;
  --panel-line:#a3a3a3;
  --field:#ffffff;
  --rule:#8c8c8c;
  --btn-bg:#f1f1f1;
  --btn-line:#c9c9c9;
  --foot-line:#8aa0c8;
  --foot-glow:#fbf3c6;
}
*{box-sizing:border-box;margin:0;padding:0}
html,body{width:1159px;height:1200px;overflow:hidden;background:#fff}
body{position:relative;font-family:Arimo,Arial,sans-serif;color:var(--ink)}
.page{position:absolute;inset:0}
.post{position:absolute;left:94px;width:675px}
.post-title{font-size:17px;font-weight:400;color:var(--title);padding-bottom:4px;border-bottom:1px dashed var(--rule)}
.meta{font-size:9px;color:var(--meta);margin-top:12px}
.meta a{color:var(--link);font-weight:700;text-decoration:underline}
.share{display:flex;gap:5px;margin-top:7px;align-items:center}
.share-btn{display:flex;align-items:center;gap:4px;height:18px;padding:0 6px;border:1px solid var(--btn-line);border-radius:3px;background:var(--btn-bg);font-size:10px;color:#666}
.share-btn i{display:block;width:10px;height:10px;background:#7aa4d8;border-radius:2px}
.share-btn.like i{background:#4a66a0}
.count{height:18px;padding:0 6px;border:1px solid var(--btn-line);font-size:10px;line-height:16px;color:#444;background:#fff}
.body{margin-top:20px;padding-left:3px;font-size:11.4px;line-height:17.6px}
.body p{margin-bottom:17.6px}
.figure{float:right;border:1px solid #c6c6c6;padding:3px;background:#fff;margin-left:14px;margin-top:-28px}
.figure div{width:100%;height:100%}
.more{font-size:10.5px;color:var(--more);text-decoration:underline;display:inline-block}
.side{position:absolute;left:788px;width:299px}
.panel{background:var(--panel);border-radius:7px;padding:8px 10px;color:#fff}
.panel h2{font-size:18px;font-weight:400;padding-bottom:6px;border-bottom:1px solid var(--panel-line)}
.label{font-size:14px;margin:6px 0 3px 3px}
.field{height:22px;background:var(--field);border:1px solid #ccc;font-size:10px;color:#999;padding:4px 5px}
.login-row{display:flex;align-items:center;margin-top:10px;font-size:10.5px}
.login{background:#111;color:#fff;border-radius:4px;padding:5px 18px;font-size:12px;margin-right:12px}
.login-row b{text-decoration:underline;margin-left:6px}
.bios{display:grid;grid-template-columns:repeat(4,63px);gap:9px 9px;margin-top:20px;padding-bottom:13px;border-bottom:1px solid var(--panel-line)}
.bio{height:59px;border:2px solid #fff;background:linear-gradient(135deg,#b7cf7a,#e3c6a8 60%,#d9e6b5)}
.read{text-align:right;font-size:11.5px;font-style:italic;text-decoration:underline;margin:17px 4px 10px}
.footer{position:absolute;left:94px;top:1133px;width:980px;height:67px;border-top:2px solid var(--foot-line);background:radial-gradient(ellipse at 50% 0%,var(--foot-glow),#fff 70%)}
.nav{position:absolute;left:16px;top:25px;font-size:10.5px;display:flex;gap:0}
.nav span{padding:0 8px;border-right:1px solid #333}
.nav span:first-child{padding-left:0}
.nav span:last-child{border:0}
.copy{position:absolute;left:16px;top:46px;font-size:10.5px}
.sub{position:absolute;left:720px;top:13px;width:245px}
.sub h3{font-size:13.5px;font-weight:400}
.sub .field{display:flex;justify-content:space-between;align-items:center;margin-top:4px;border:1px solid #888;border-radius:4px;height:24px}
</style>
</head>
<body>
<div class="page">

<article class="post" style="top:0">
  <h1 class="post-title">Lorel IPsum Dolor sit amet</h1>
  <div class="meta">Posted at 11:55 PM in <a>Lin Avery</a>, <a>Podcasts</a> | <a>Permalink</a> | <a>Comments (0)</a></div>
  <div class="share">
    <span class="share-btn"><i></i>Reblog (0)</span>
    <span class="share-btn"><i></i>Post This!</span>
    <span class="share-btn like"><i></i>Like</span><span class="count">2</span>
    <svg width="20" height="14" viewBox="0 0 20 14"><rect x="1" y="1" width="18" height="12" fill="#f2c230" stroke="#c99a10"/><path d="M1 1l9 7 9-7" fill="none" stroke="#c99a10"/></svg>
  </div>
  <div class="body">
    <div class="figure" style="width:268px;height:385px"><div role="img" aria-label="Stacked coloured letter cubes spelling a brand word" style="background:linear-gradient(180deg,#e54545 0%,#e54545 30%,#5cb85c 30%,#5cb85c 50%,#2a9fc0 50%,#2a9fc0 68%,#f2c230 68%,#f2c230 82%,#e54545 82%,#f4f4f4 100%)"></div></div>
    <p>LAV is the creator, co-founder and host of the Maple Crew podcast, the edgiest show on Spellbound Cards available online.&nbsp; Even with the success of this podcast, he has always wanted to do something that was safe for work and here it is, an interview with the only Canadian player inducted in the Hall of Fame, Dale Morrow.&nbsp; Dale has included some excellent advice not only for players of the game, but writers as well.</p>
    <p>LAV is the creator, co-founder and host of the Maple Crew podcast, the edgiest show on Spellbound Cards available online.&nbsp; Even with the success of this podcast, he has always wanted to do something that was safe for work and here it is, an interview with the only Canadian player inducted in the Hall of Fame, Dale Morrow.&nbsp; Dale has included some excellent advice not only for players of the game, but writers as well.LAV is the creator, co-founder and host of the Maple Crew podcast, the edgiest show on Spellbound Cards available online.&nbsp; Even with the success of this podcast, he has always wanted to do something that was safe for work and here it is, an interview with the only Canadian player inducted in the Hall of Fame, Dale Morrow.&nbsp; Dale has included some excellent advice not only for players of the game, but writers as well.</p>
    <p style="clear:both">LAV is the creator, co-founder and host of the Maple Crew podcast, the edgiest show on Spellbound Cards available online. Even with the success of this podcast, he has always wanted to do something that was safe for work and here it is, an interview with the only Canadian player inducted in the Hall of Fame, Dale Morrow.&nbsp; Dale has included some excellent advice not only for players of the game, but writers as well.</p>
    <p>LAV is the creator, co-founder and host of the Maple Crew podcast, the edgiest show on Spellbound Cards available online. Even with the success of this podcast, he has always wanted to do something that was safe for work and here it is, an interview with the only Canadian player inducted in the Hall of Fame, Dale Morrow.</p>
    <a class="more">Continue Reading</a>
  </div>
</article>

<article class="post" style="top:667px">
  <h1 class="post-title">Lorel IPsum Dolor sit amet</h1>
  <div class="meta">Posted at 11:55 PM in <a>Lin Avery</a>, <a>Podcasts</a> | <a>Permalink</a> | <a>Comments (0)</a></div>
  <div class="share">
    <span class="share-btn"><i></i>Reblog (0)</span>
    <span class="share-btn"><i></i>Post This!</span>
    <span class="share-btn like"><i></i>Like</span><span class="count">2</span>
    <svg width="20" height="14" viewBox="0 0 20 14"><rect x="1" y="1" width="18" height="12" fill="#f2c230" stroke="#c99a10"/><path d="M1 1l9 7 9-7" fill="none" stroke="#c99a10"/></svg>
  </div>
  <div class="body">
    <div class="figure" style="width:281px;height:307px"><div role="img" aria-label="Green figure pushing a shopping cart among red discount cubes" style="background:radial-gradient(circle at 70% 55%,#8fd45a 0 14%,transparent 15%),radial-gradient(circle at 40% 60%,#d8322e 0 22%,#fff 45%)"></div></div>
    <p>LAV is the creator, co-founder and host of the Maple Crew podcast, the edgiest show on Spellbound Cards available online.&nbsp; Even with the success of this podcast, he has always wanted to do something that was safe for work and here it is, an interview with the only Canadian player inducted in the Hall of Fame, Dale Morrow.&nbsp; Dale has included some excellent advice not only for players of the game, but writers as well.</p>
    <p>LAV is the creator, co-founder and host of the Maple Crew podcast, the edgiest show on Spellbound Cards available online.&nbsp; Even with the success of this podcast, he has always wanted to do something that was safe for work and here it is, an interview with the only Canadian player inducted in the Hall of Fame, Dale Morrow.&nbsp; Dale has included some excellent advice not only for players of the game, but writers as well.</p>
    <a class="more">Continue Reading</a>
  </div>
</article>

<aside class="side" style="top:0">
  <div class="panel" style="height:12px;border-radius:0 0 7px 7px;padding:0"></div>
  <div class="panel" style="margin-top:10px;height:182px">
    <h2>Sign In</h2>
    <div class="label">User id</div>
    <div class="field">Type Your User id here</div>
    <div class="label">Password</div>
    <div class="field">••••••••••••••••</div>
    <div class="login-row"><span class="login">Login</span>Forgot your password? <b>Click here</b></div>
  </div>
  <div class="panel" style="margin-top:10px">
    <h2>Bios</h2>
    <div class="bios">
      <div class="bio" role="img" aria-label="Staff portrait"></div><div class="bio" role="img" aria-label="Staff portrait"></div><div class="bio" role="img" aria-label="Staff portrait"></div><div class="bio" role="img" aria-label="Staff portrait"></div>
      <div class="bio" role="img" aria-label="Staff portrait"></div><div class="bio" role="img" aria-label="Staff portrait"></div><div class="bio" role="img" aria-label="Staff portrait"></div><div class="bio" role="img" aria-label="Staff portrait"></div>
    </div>
    <div class="read">Read More Bios</div>
  </div>
</aside>

<footer class="footer">
  <nav class="nav"><span>Home</span><span>Bios</span><span>Product Review</span><span>Activities</span><span>Case Studies</span><span>Discussion</span><span>Glossary</span><span>FAQ</span><span>Contact</span></nav>
  <div class="copy">© 2012, All Rights Reserved</div>
  <div class="sub">
    <h3>Subscribe Newsletter</h3>
    <div class="field">Type your email id
      <svg width="16" height="16" viewBox="0 0 16 16"><rect x="1" y="1" width="14" height="14" fill="#fff" stroke="#333"/><path d="M4 8l3 3 6-8" fill="none" stroke="#111" stroke-width="2"/></svg>
    </div>
  </div>
</footer>

</div>
</body>
</html>
```